New Business Card Design for Manufacturing

We are an engineering/manufacturing company that offers Advanced machining/assembly/engineering services, as well as innovative products for the heavy duty engine cooling markets.

We are looking to get a new business card designed that is clean and modern looking, but still fits the wide range of technical/skilled work we do.

- We hope to use this design as the base for other design work in new Presentations, web, and print work.

Industry/Entity Type

Engineering

Contact Information for Business Card

Our preferred color of blue is (RGB) 22/71/159 but can vary slightly from that color. Our content will be our Logo and full company name (Vantrell Forge Works, Inc.), company address, name, job title, phone number with extension, cell number, fax number, website, and email address on the cards.
We'd like the full company name next to the logo, but we are open to other interpretations of that layout.
Preferably, we would like the back side to be clean with just our logo, and the front to contain all of the contact information.

Colors
2f74b4
0355a3
85abd2

Requirements
Must have
• - Logo, company name, needed content - We are open to interpretation beyond that.
• - Standard size business card.
• - Horizontal orientation.
• - Enough space for lengthy names / job titles (for example, a job title could read "Directory of Human Resources" or "V.P. of Governmental Affairs"). We need this to look clean, whether the title be short (CEO) or long (as described above).

```html
<!DOCTYPE html>
<html lang="en">
<head>
<meta charset="UTF-8">
<title>Vantrell Forge Works – Business Card</title>
<link rel="stylesheet" href="https://fonts.googleapis.com/css2?family=Open+Sans:wght@400;600;700;800&display=swap">
<style>
  :root {
    --brand-blue: #16479f;
    --blue-mid: #0355a3;
    --blue-bright: #2f74b4;
    --blue-light: #85abd2;
    --steel-grey: #9aa3ad;
    --ink-grey: #6b7079;
    --paper: #ffffff;
    --stage: #e9ebee;
  }
  * { margin: 0; padding: 0; box-sizing: border-box; }
  html, body {
    width: 1200px; height: 716px; overflow: hidden;
    background: var(--stage);
    font-family: "Open Sans", Arial, sans-serif;
  }
  .card-set {
    position: absolute; inset: 0;
    display: flex; align-items: center; justify-content: center; gap: 40px;
  }
  .card {
    position: relative; width: 520px; height: 297px; overflow: hidden;
    box-shadow: 0 6px 18px rgba(0,0,0,.18);
  }

  /* Back side */
  .card-back { background: var(--brand-blue); color: var(--paper); }
  .card-back .wordmark {
    position: absolute; left: 70px; top: 104px;
    display: flex; align-items: center; gap: 14px;
    font-size: 40px; font-weight: 800; letter-spacing: 1px; color: var(--paper);
  }
  .wordmark .mark-square { width: 30px; height: 30px; background: currentColor; }
  .card-back .web {
    position: absolute; left: 70px; bottom: 60px; font-size: 11px; opacity: .9;
  }

  /* Front side */
  .card-front { background: var(--paper); }
  .card-front .band { position: absolute; inset: 0; }
  .holder { position: absolute; left: 34px; top: 34px; }
  .holder .name {
    font-size: 20px; font-weight: 800; color: var(--brand-blue); letter-spacing: .5px;
  }
  .holder .title { font-size: 11px; color: var(--ink-grey); margin-top: 2px; }
  .card-front .wordmark {
    position: absolute; right: 34px; top: 78px;
    display: flex; align-items: center; gap: 10px;
    font-size: 27px; font-weight: 800; letter-spacing: .5px; color: var(--brand-blue);
  }
  .wordmark .mark-square.small { width: 20px; height: 20px; }
  .contact-list {
    position: absolute; left: 30px; top: 150px; list-style: none;
    color: var(--paper); font-size: 12px;
  }
  .contact-list li { display: flex; align-items: center; gap: 8px; height: 20px; }
  .contact-list svg { width: 11px; height: 11px; fill: var(--paper); }
  .card-front .web {
    position: absolute; left: 30px; top: 240px; color: var(--paper); font-size: 12px;
  }
  .company {
    position: absolute; right: 30px; top: 196px; text-align: right; color: var(--paper);
  }
  .company .legal-name { font-size: 12px; color: var(--blue-light); margin-bottom: 6px; }
  .company .address { font-size: 13px; line-height: 1.4; }
</style>
</head>
<body>
<main class="card-set">
  <section class="card card-back" aria-label="Card back">
    <div class="wordmark"><span class="mark-square"></span>VANTRELL FORGE</div>
    <p class="web">www.vantrellforge.com</p>
  </section>

  <section class="card card-front" aria-label="Card front">
    <svg class="band" viewBox="0 0 520 297" preserveAspectRatio="none" aria-hidden="true">
      <polygon points="0,128 170,128 186,140 520,140 520,297 0,297" fill="var(--brand-blue)"/>
      <polygon points="186,140 520,140 520,150 196,150" fill="var(--blue-bright)"/>
      <polygon points="300,186 520,186 520,190 304,190" fill="var(--steel-grey)"/>
      <polygon points="150,232 330,232 340,240 160,240" fill="var(--blue-light)"/>
      <polygon points="340,240 520,240 520,244 344,244" fill="var(--steel-grey)"/>
      <polygon points="0,262 140,262 150,270 0,270" fill="var(--blue-mid)"/>
      <polygon points="0,270 520,270 520,297 0,297" fill="var(--blue-mid)"/>
    </svg>

    <div class="holder">
      <h1 class="name">DORIAN KESSEL</h1>
      <p class="title">President</p>
    </div>

    <div class="wordmark"><span class="mark-square small"></span>VANTRELL FORGE</div>

    <ul class="contact-list">
      <li><svg viewBox="0 0 12 12"><path d="M2 1h3l1 3-2 1a7 7 0 0 0 3 3l1-2 3 1v3c-6 0-9-3-9-9z"/></svg>+000.000.00.00</li>
      <li><svg viewBox="0 0 12 12"><path d="M3 0h6v12H3zM4 1v9h4V1z"/></svg>+000.000.00.00</li>
      <li><svg viewBox="0 0 12 12"><path d="M3 0h6v3H3zM1 4h10v6H9v2H3v-2H1zM4 8v3h4V8z"/></svg>+000.000.00.00</li>
      <li><svg viewBox="0 0 12 12"><path d="M0 2h12v8H0zM1 3l5 4 5-4z"/></svg>+000.000.00.00</li>
    </ul>
    <p class="web">www.vantrellforge.com</p>

    <div class="company">
      <p class="legal-name">Vantrell Forge Works, Inc.</p>
      <p class="address">Street Name Avenue, Suite<br>100 State, Zip Code, Country</p>
    </div>
  </section>
</main>
</body>
</html>
```